Call Center In Need of Website Design

We are a call center that provides inbound and outbound calling & marketing services for eCommerce store. We would like to see a fun, creative, playful design that is simple.

Here are some sample design sites we like;
- https://www.velmoreline.com/
- https://pindrask.io/
- https://www.glimbertic.com/live-chat-software/
- https://www.zavrolin.com/

Here are some competitor sites;
- https://www.ostrevaglinks.com/
- https://www.helpkestrel.com/

I have attached website content for your use.

Target Market(s)

eCommerce

Coding

Coded - Design and coding required

Number of Pages Required

5+ page

Font styles to use
Sans Serif

Colors

Designer to choose colors to be used in the design.

Requirements
Must have
• Must have designs for the following 5 separate pages;
• 1. Home (landing)
• - This will be were the design style really needs to show.
• - Just needs to touch on key services
• - CTA
• 2. About Us
• - Basic page for about me paragraph
• 3. Services
• - List of services with icons
• - Click on service type to expand details or hover over service icon to view popup bubble with details about that service
• 4. Pricing
• - Option to bundle 1(one) digital service plan and 1(one) call center service plan
• - Bundling adds 10% monthly discount to over all price
• - Customer does NOT have to bundle
• - FAQ
• 5. Contact Us
• - Include a capture form (name, company name, email, phone, message)
• - Contact info
• - Business hours
• When customer purchases their desired plan, then they are taken to a page where they must schedule a call with an account rep.
Nice to have
• home page animations
Should not have
• All information on Home/Landing page.

```html
<!DOCTYPE html>
<html lang="en">
<head>
<meta charset="utf-8">
<title>Orbitalle – 24x7 Live Call Answering Service</title>
<link rel="stylesheet" href="https://fonts.googleapis.com/css2?family=Montserrat:wght@400;500;600;700&family=Open+Sans:wght@400;600&display=swap">
<style>
  :root {
    --teal: #5bbd9c;
    --teal-dark: #46a585;
    --ink: #1e1e1e;
    --text: #3c3c3c;
    --logo-grey: #555a5c;
    --mint: #e2f3ee;
    --mint-soft: #eef8f5;
    --line: #d4e6e0;
    --white: #ffffff;
    --social: #2c4a86;
  }
  * { box-sizing: border-box; margin: 0; padding: 0; }
  html, body { width: 1200px; height: 2378px; overflow: hidden; background: var(--white); }
  body { position: relative; font-family: "Open Sans", Arial, sans-serif; color: var(--text); }
  .abs { position: absolute; }

  /* Header */
  .site-header { position: absolute; left: 0; top: 0; width: 1200px; height: 100px; z-index: 2; }
  .brand { display: flex; align-items: center; gap: 18px; }
  .brand-dot { width: 58px; height: 58px; border: 5px solid var(--teal); border-radius: 50%; }
  .brand-name { font-family: "Montserrat", Arial, sans-serif; font-weight: 400; color: var(--logo-grey); letter-spacing: 7px; }
  .site-brand { left: 75px; top: 30px; }
  .site-brand .brand-name { font-size: 36px; }
  .main-nav { left: 632px; top: 14px; display: flex; }
  .main-nav a { font-family: "Open Sans", Arial, sans-serif; font-size: 13px; color: var(--ink); text-decoration: none; padding: 7px 13px; margin-right: 10px; border-radius: 3px; }
  .main-nav a.active { background: var(--teal); color: var(--white); font-weight: 600; }

  /* Hero */
  .hero-photo { left: 0; top: 0; width: 1200px; height: 700px; background: linear-gradient(110deg, #f3f5f6 0%, #e6eaec 40%, #c9d3d9 62%, #e9eef1 100%); }
  .hero-title { left: 175px; top: 258px; font-size: 37px; line-height: 47px; font-weight: 600; color: var(--ink); }
  .hero-text { left: 176px; top: 366px; width: 340px; font-size: 14.5px; line-height: 19px; color: var(--ink); }
  .btn { left: 179px; top: 437px; width: 177px; height: 50px; background: var(--teal); color: var(--white); font-family: "Montserrat", Arial, sans-serif; font-weight: 600; font-size: 16px; display: flex; align-items: center; justify-content: center; gap: 8px; text-decoration: none; }

  /* Welcome band */
  .welcome-band { left: 0; top: 640px; }
  .welcome-kicker { left: 388px; top: 886px; font-family: "Montserrat", Arial, sans-serif; font-weight: 700; font-size: 16px; color: var(--white); }
  .welcome-name { left: 386px; top: 904px; font-family: "Montserrat", Arial, sans-serif; font-weight: 700; font-size: 32px; color: var(--white); }
  .welcome-text { left: 652px; top: 818px; width: 205px; font-size: 14px; line-height: 17.5px; color: var(--white); }
  .welcome-more { left: 712px; top: 983px; font-family: "Montserrat", Arial, sans-serif; font-weight: 700; font-size: 14px; color: var(--white); text-decoration: none; }

  /* Services */
  .section-title { left: 0; width: 1200px; top: 1152px; text-align: center; font-family: "Montserrat", Arial, sans-serif; font-weight: 700; font-size: 24px; color: var(--ink); }
  .section-rule { left: 577px; top: 1211px; width: 48px; height: 5px; border-radius: 3px; background: #dcdcdc; }
  .service-card { top: 1345px; width: 374px; background: var(--white); border: 1px solid #e6e6e6; box-shadow: 0 10px 40px rgba(0,0,0,0.07); }
  .card-digital { left: 194px; height: 492px; }
  .card-call { left: 621px; height: 495px; }
  .service-icon { top: 1288px; width: 162px; height: 162px; border-radius: 50%; background: var(--teal); display: flex; align-items: center; justify-content: center; }
  .icon-digital { left: 291px; }
  .icon-call { left: 719px; }
  .service-title { font-family: "Montserrat", Arial, sans-serif; font-weight: 600; font-size: 19px; color: var(--ink); position: absolute; top: 150px; left: 53px; }
  .service-title::after { content: ""; position: absolute; left: 0; top: 37px; width: 55px; height: 4px; background: var(--teal); }
  .service-list { position: absolute; top: 217px; left: 53px; list-style: none; font-size: 11.5px; line-height: 20px; color: var(--ink); }
  .card-call .service-list { top: 213px; }
  .service-list li { padding-left: 17px; position: relative; }
  .service-list li::before { content: ""; position: absolute; left: 0; top: 7px; border-left: 4px solid var(--ink); border-top: 3px solid transparent; border-bottom: 3px solid transparent; }

  /* Footer */
  .footer-bg { left: 0; top: 1930px; }
  .footer-brand { left: 133px; top: 2066px; }
  .footer-brand .brand-dot { width: 66px; height: 66px; }
  .footer-brand .brand-name { font-size: 36px; }
  .footer-col h4 { font-family: "Montserrat", Arial, sans-serif; font-weight: 700; font-size: 12px; color: var(--teal); margin-bottom: 18px; }
  .footer-col { top: 2060px; font-size: 12px; color: var(--ink); }
  .col-contact { left: 533px; }
  .col-menu { left: 761px; }
  .col-social { left: 933px; }
  .contact-row { display: flex; gap: 12px; margin-bottom: 20px; line-height: 17px; }
  .contact-row svg { flex: none; margin-top: 2px; }
  .menu-list { list-style: none; line-height: 17.5px; }
  .social-row { display: flex; align-items: center; gap: 13px; margin-bottom: 10px; }
  .social-dot { width: 28px; height: 28px; border-radius: 50%; background: var(--social); }
  .footer-rule { left: 128px; top: 2275px; width: 940px; height: 1px; background: var(--line); }
  .copyright { left: 0; width: 1200px; top: 2322px; text-align: center; font-size: 11px; color: var(--ink); }
</style>
</head>
<body>

<section class="hero">
  <div class="abs hero-photo" role="img" aria-label="Photo of a smiling call center agent wearing a headset in a bright office, with a colleague blurred behind"></div>
  <h1 class="abs hero-title">24x7 Live Call<br>Answering Service</h1>
  <p class="abs hero-text">Orbitalle is an omnichannel provider for customer care and back-end office support.</p>
  <a class="abs btn" href="#">Read More <span>&raquo;</span></a>
</section>

<header class="site-header">
  <div class="abs brand site-brand"><span class="brand-dot"></span><span class="brand-name">ORBITALLE</span></div>
  <nav class="abs main-nav">
    <a class="active" href="#">HOME</a>
    <a href="#">ABOUT US</a>
    <a href="#">SERVICES</a>
    <a href="#">PRICING</a>
    <a href="#">CONTACT US</a>
  </nav>
</header>

<section class="welcome">
  <svg class="abs welcome-band" width="1200" height="430" viewBox="0 0 1200 430" aria-hidden="true">
    <path d="M0 5 Q600 85 1200 5 L1200 382 Q600 452 0 382 Z" fill="var(--teal)"/>
    <circle cx="760" cy="245" r="150" fill="none" stroke="var(--white)" stroke-width="14"/>
  </svg>
  <p class="abs welcome-kicker">WELCOME TO</p>
  <p class="abs welcome-name">ORBITALLE</p>
  <p class="abs welcome-text">Orbitalle is an omnichannel provider for customer care and back-end office support. We primarily work with eCommerce companies around the world.</p>
  <a class="abs welcome-more" href="#">READ MORE &#9656;</a>
</section>

<section class="services">
  <h2 class="abs section-title">OUR SERVICES</h2>
  <div class="abs section-rule"></div>

  <article class="abs service-card card-digital">
    <h3 class="service-title">Digital Services</h3>
    <ul class="service-list">
      <li>Email Support</li>
      <li>Live Chat Support</li>
      <li>Product Research</li>
      <li>Product Listing</li>
      <li>Price Monitoring</li>
      <li>Product Photo &amp; Video Editing</li>
    </ul>
  </article>
  <article class="abs service-card card-call">
    <h3 class="service-title">Call Center Services</h3>
    <ul class="service-list">
      <li>Answering service</li>
      <li>Welcome Calls</li>
      <li>Follow-Up Service</li>
      <li>Customer Upselling</li>
      <li>Over-The-Phone Order Taking</li>
      <li>Order Return Processing</li>
      <li>Feedback/Survey Calls</li>
      <li>Message Delivering Service</li>
      <li>ROI Diagnostics &amp; Reporting</li>
      <li>Scalable Call Center Pricing</li>
      <li>Customizable For Any Industry</li>
      <li>100% US-Based Agents</li>
    </ul>
  </article>

  <div class="abs service-icon icon-digital">
    <svg width="90" height="90" viewBox="0 0 90 90" fill="none" stroke="var(--white)" stroke-width="3" aria-hidden="true">
      <rect x="14" y="6" width="62" height="44" rx="2"/>
      <circle cx="45" cy="27" r="9"/>
      <path d="M38 50 L36 60 H54 L52 50"/>
      <rect x="8" y="64" width="66" height="18" rx="2"/>
      <path d="M14 70 H68 M14 76 H68"/>
      <rect x="78" y="66" width="9" height="14" rx="4"/>
    </svg>
  </div>
  <div class="abs service-icon icon-call">
    <svg width="90" height="90" viewBox="0 0 90 90" fill="none" stroke="var(--white)" stroke-width="3" aria-hidden="true">
      <path d="M16 56 V44 A27 27 0 0 1 70 44 V56"/>
      <rect x="10" y="50" width="12" height="22" rx="5" fill="var(--white)"/>
      <rect x="64" y="50" width="12" height="22" rx="5" fill="var(--white)"/>
      <path d="M70 70 Q70 82 52 82 H46"/>
      <path d="M42 6 H82 V32 H58 L50 40 V32 H42 Z" fill="var(--white)"/>
      <path d="M48 15 H76 M48 22 H70" stroke="var(--teal)"/>
    </svg>
  </div>
</section>

<footer>
  <svg class="abs footer-bg" width="1200" height="448" viewBox="0 0 1200 448" aria-hidden="true">
    <path d="M0 45 Q600 -35 1200 35 L1200 448 L0 448 Z" fill="var(--mint-soft)"/>
    <path d="M0 65 Q600 -5 1200 60 L1200 448 L0 448 Z" fill="var(--mint)"/>
  </svg>
  <div class="abs brand footer-brand"><span class="brand-dot"></span><span class="brand-name">ORBITALLE</span></div>

  <div class="abs footer-col col-contact">
    <h4>CONTACT US</h4>
    <div class="contact-row">
      <svg width="10" height="13" viewBox="0 0 10 13" aria-hidden="true"><path d="M5 0 A5 5 0 0 1 10 5 C10 8 5 13 5 13 C5 13 0 8 0 5 A5 5 0 0 1 5 0 Z" fill="var(--ink)"/><circle cx="5" cy="5" r="2" fill="var(--mint)"/></svg>
      <span>418 Larkmoor Ave.<br>Delvana, CA 90412</span>
    </div>
    <div class="contact-row">
      <svg width="11" height="11" viewBox="0 0 24 24" aria-hidden="true"><path d="M6.6 10.8a15 15 0 0 0 6.6 6.6l2.2-2.2c.3-.3.7-.4 1-.2 1.1.4 2.3.6 3.6.6.6 0 1 .4 1 1V20c0 .6-.4 1-1 1A17 17 0 0 1 3 4c0-.6.4-1 1-1h3.5c.6 0 1 .4 1 1 0 1.3.2 2.5.6 3.6.1.3 0 .7-.2 1z" fill="var(--ink)"/></svg>
      <span>(800) 555-0147</span>
    </div>
    <div class="contact-row">
      <svg width="12" height="10" viewBox="0 0 12 10" aria-hidden="true"><rect x="0" y="0" width="12" height="10" rx="1" fill="var(--ink)"/><path d="M0.5 1 L6 5.5 L11.5 1" fill="none" stroke="var(--mint)" stroke-width="1.2"/></svg>
      <span>info@orbitalle.com</span>
    </div>
  </div>

  <div class="abs footer-col col-menu">
    <h4>MENU</h4>
    <ul class="menu-list">
      <li>Home</li>
      <li>About Us</li>
      <li>Services</li>
      <li>Pricing</li>
      <li>Contact</li>
    </ul>
  </div>

  <div class="abs footer-col col-social">
    <h4>CONNECT WITH US</h4>
    <div class="social-row"><span class="social-dot"></span><span>Friendlane</span></div>
    <div class="social-row"><span class="social-dot"></span><span>Chirpwave</span></div>
    <div class="social-row"><span class="social-dot"></span><span>Linkvault</span></div>
  </div>

  <div class="abs footer-rule"></div>
  <p class="abs copyright">Copyrights @ 2018 All Rights Reserved</p>
</footer>

</body>
</html>
```